Business Card for Coastal Tundrabridge Advisory

We need a business card for Coastal Tundrabridge Advisory. The company website address is provided below. The company logo is attached. We provide specialized permafrost services to the mining, transportation, and oil & gas industries. The card should be prepared for:
Matthias Korhonen, PhD.
Coastal Tundrabridge Advisory
PO Box 418259
Quillwater, Alaska 99642
Direct: +1-907-555-0143
Email: mkorhonen@tundrabridgeadvisory.example
Website: www.coastaltundrabridgeadvisory.example

```html
<!DOCTYPE html>
<html lang="en">
<head>
<meta charset="utf-8">
<title>Coastal Tundrabridge Advisory – Business Card</title>
<link rel="stylesheet" href="https://fonts.googleapis.com/css2?family=Montserrat:wght@400;600;700&display=swap">
<style>
  :root {
    --backdrop: #1b1c1e;
    --card-dark: #111822;
    --card-dark-mark: #1f2a37;
    --card-light: #ffffff;
    --ink: #131a24;
    --ink-soft: #2b2f36;
  }
  * { box-sizing: border-box; margin: 0; padding: 0; }
  html, body {
    width: 1200px; height: 1059px; overflow: hidden;
    background: var(--backdrop);
    font-family: "Montserrat", sans-serif;
  }
  .canvas { position: relative; width: 1200px; height: 1059px; }
  .card {
    position: absolute; left: 254px; width: 692px; height: 392px;
    border-radius: 18px; overflow: hidden;
  }
  .card--front { top: 89px; background: var(--card-dark); }
  .card--back { top: 546px; background: var(--card-light); color: var(--ink-soft); }

  .front-name {
    position: absolute; left: 0; right: 0; top: 150px;
    text-align: center; font-weight: 600; font-size: 34px;
    color: var(--card-dark-mark); letter-spacing: 0.5px;
  }

  .brand {
    position: absolute; left: 27px; top: 24px;
    display: flex; align-items: center; gap: 10px;
    font-weight: 700; font-size: 20px; color: var(--ink);
  }
  .brand__square { width: 16px; height: 16px; background: var(--ink); }

  .holder {
    position: absolute; right: 22px; top: 172px; text-align: right;
  }
  .holder__name { font-weight: 700; font-size: 21px; color: var(--ink); line-height: 28px; }
  .holder__company { font-size: 17px; line-height: 24px; color: var(--ink-soft); }
  .holder-bar {
    position: absolute; right: 0; top: 172px; width: 11px; height: 50px; background: var(--ink);
  }

  .address {
    position: absolute; left: 26px; top: 212px;
    font-size: 17px; line-height: 28px;
  }
  .contact {
    position: absolute; left: 27px; top: 293px;
    font-size: 17px; line-height: 27px; list-style: none;
  }
  .contact__label { font-weight: 600; color: var(--ink); }
</style>
</head>
<body>
<main class="canvas">
  <section class="card card--front" aria-label="Card front">
    <p class="front-name">Coastal Tundrabridge Advisory</p>
  </section>

  <section class="card card--back" aria-label="Card back">
    <div class="brand"><span class="brand__square"></span>Coastal Tundrabridge Advisory</div>

    <div class="holder">
      <p class="holder__name">Matthias Korhonen, PhD</p>
      <p class="holder__company">Coastal Tundrabridge Advisory</p>
    </div>
    <span class="holder-bar"></span>

    <address class="address" style="font-style: normal;">
      PO Box 418259<br>
      Quillwater, Alaska 99642
    </address>

    <ul class="contact">
      <li><span class="contact__label">Direct:</span> +1-907-555-0143</li>
      <li><span class="contact__label">Email:</span> mkorhonen@tundrabridgeadvisory.example</li>
      <li><span class="contact__label">Website:</span> www.coastaltundrabridgeadvisory.example</li>
    </ul>
  </section>
</main>
</body>
</html>
```